Business Card Design - Amberfield Court

We are looking at a new design for our business cards that has a modern and professional look. We run a residential aged care facility focussing on the care of residents. The cards will be used for potential clients, consultants and business opportunities in this sector. Blue and white is our main colours and would to see these colours incorporated in the design.
Industry/Entity Type
Business
Contact Information for Business Card
Amberfield Court, Darren Walsh, dwalsh@amberfieldcourt.com.au, Finance Manager, 0472 639 208, BCom, 37 Marrabel Crescent, Brindle Vale, Qld 4093.
Look and feel
Each slider illustrates characteristics of the customer's brand and the style your logo design should communicate.

```html
<!DOCTYPE html>
<html lang="en">
<head>
<meta charset="utf-8">
<title>Amberfield Court – Business Card</title>
<link href="https://fonts.googleapis.com/css2?family=Open+Sans:wght@400;600;700&display=swap" rel="stylesheet">
<style>
  :root {
    --backdrop: #e7e5e2;
    --card-black: #0e0f10;
    --card-black-soft: #25272a;
    --brand-blue: #7fb7cc;
    --dome-white: #f1f3f5;
    --dome-rim: #c8beb6;
    --ink-grey: #3d4145;
    --icon-grey: #8b9298;
    --white: #ffffff;
  }
  * { box-sizing: border-box; margin: 0; padding: 0; }
  html, body { width: 1200px; height: 1023px; overflow: hidden; }
  body {
    background: var(--backdrop);
    font-family: "Open Sans", Arial, sans-serif;
    position: relative;
  }
  .card {
    position: absolute;
    top: 240px;
    width: 330px;
    height: 540px;
    border-radius: 6px;
    overflow: hidden;
    background: linear-gradient(160deg, var(--card-black-soft) 0%, var(--card-black) 55%, #050506 100%);
    box-shadow: 0 10px 30px rgba(0,0,0,0.25);
  }
  .card--front { left: 195px; }
  .card--back { left: 675px; }

  .brand {
    position: absolute;
    left: 0; right: 0;
    display: flex;
    align-items: center;
    justify-content: center;
    gap: 10px;
  }
  .card--front .brand { top: 120px; }
  .card--back .brand { top: 215px; }
  .brand__dot {
    width: 22px; height: 22px;
    border-radius: 50%;
    background: var(--brand-blue);
  }
  .brand__name {
    font-size: 22px;
    font-weight: 600;
    letter-spacing: 1px;
    text-transform: uppercase;
    color: var(--brand-blue);
  }
  .card--back .brand__dot { background: var(--dome-white); }
  .card--back .brand__name { color: var(--dome-white); }

  .person {
    position: absolute;
    top: 238px;
    left: 0; right: 0;
    text-align: center;
  }
  .person__name {
    font-size: 21px;
    font-weight: 700;
    letter-spacing: 0.5px;
    text-transform: uppercase;
    color: var(--brand-blue);
  }
  .person__role {
    margin-top: 2px;
    font-size: 12px;
    font-weight: 600;
    letter-spacing: 0.5px;
    text-transform: uppercase;
    color: var(--white);
  }

  .contact-dome {
    position: absolute;
    left: 0;
    bottom: -6px;
    width: 330px;
    height: 216px;
    border: 6px solid var(--dome-rim);
    border-bottom: none;
    border-radius: 165px 165px 0 0;
    background: var(--dome-white);
    padding-top: 40px;
    text-align: center;
    color: var(--ink-grey);
    font-size: 12.5px;
    line-height: 1.45;
  }
  .contact__icon {
    display: block;
    margin: 0 auto 2px;
    width: 14px; height: 14px;
  }
  .contact__line { display: block; }
  .contact__line + .contact__icon { margin-top: 6px; }
  .contact__address {
    margin-top: 8px;
    text-transform: uppercase;
    letter-spacing: 0.3px;
  }
</style>
</head>
<body>

  <section class="card card--front" aria-label="Business card front">
    <div class="brand">
      <span class="brand__dot"></span>
      <span class="brand__name">Amberfield Court</span>
    </div>

    <div class="person">
      <p class="person__name">Darren Walsh</p>
      <p class="person__role">Finance Manager</p>
    </div>

    <div class="contact-dome">
      <svg class="contact__icon" viewBox="0 0 14 14" aria-hidden="true">
        <rect width="14" height="14" rx="2" fill="var(--icon-grey)"/>
        <rect x="4.5" y="2.5" width="5" height="9" rx="1" fill="none" stroke="#fff" stroke-width="1.2"/>
        <circle cx="7" cy="10" r="0.6" fill="#fff"/>
      </svg>
      <span class="contact__line">0472 639 208</span>
      <svg class="contact__icon" viewBox="0 0 14 14" aria-hidden="true">
        <rect width="14" height="14" rx="2" fill="var(--icon-grey)"/>
        <rect x="2.5" y="4" width="9" height="6" fill="none" stroke="#fff" stroke-width="1.1"/>
        <path d="M2.5 4 L7 7.5 L11.5 4" fill="none" stroke="#fff" stroke-width="1.1"/>
      </svg>
      <span class="contact__line">dwalsh@amberfieldcourt.com.au</span>
      <p class="contact__address">BCom, 37 Marrabel Crescent<br>Brindle Vale, Qld 4093.</p>
    </div>
  </section>

  <section class="card card--back" aria-label="Business card back">
    <div class="brand">
      <span class="brand__dot"></span>
      <span class="brand__name">Amberfield Court</span>
    </div>
  </section>

</body>
</html>
```